Construction Company Cellar Crafters needs Business Card

I would like modern looking business card design. I am attaching logo of our company. Please include cell nr 302.418.7650 , email address cellarcrafters4u@examplemail.com, web : cellarcrafters4u.com, please also include wording: Specializing in finishing and remodeling basements. You can play with dark grey and orange colors or any ideas are welcome. Also include social media icons Friendloop and HouseGuidr.

```html
<!DOCTYPE html>
<html lang="en">
<head>
<meta charset="utf-8">
<title>Cellar Crafters – Business Card</title>
<link rel="stylesheet" href="https://fonts.googleapis.com/css2?family=Michroma&family=Open+Sans:wght@400;600&display=swap">
<style>
  :root {
    --stage: #5f5f5f;
    --card-dark: #121212;
    --orange: #f4511e;
    --orange-deep: #e8471a;
    --grey-band: #b3b3b3;
    --white: #ffffff;
    --text-light: #e6e6e6;
  }
  * { margin: 0; padding: 0; box-sizing: border-box; }
  html, body { width: 1200px; height: 900px; overflow: hidden; }
  body { background: var(--stage); position: relative; font-family: "Open Sans", sans-serif; }

  .card {
    position: absolute;
    top: 306px;
    width: 440px;
    height: 271px;
    border-radius: 10px;
    overflow: hidden;
  }
  .card--front { left: 149px; background: var(--card-dark); }
  .card--back { left: 608px; background: var(--orange); }

  .name-accent { position: absolute; left: 0; top: 35px; }
  .holder-name {
    position: absolute; left: 31px; top: 34px;
    font-family: "Michroma", sans-serif; font-size: 15px; letter-spacing: 0.5px;
    color: var(--orange); text-transform: uppercase;
  }
  .holder-title {
    position: absolute; left: 31px; top: 52px;
    font-size: 12px; color: var(--text-light);
  }

  .brand-name {
    position: absolute;
    font-family: "Michroma", sans-serif; text-transform: uppercase;
    white-space: nowrap;
  }
  .card--front .brand-name { right: 30px; top: 143px; font-size: 19px; color: var(--orange); }
  .card--back .brand-name { left: 0; right: 0; top: 135px; text-align: center; font-size: 22px; color: var(--white); }

  .contact-list { position: absolute; left: 31px; top: 185px; list-style: none; }
  .contact-list li {
    display: flex; align-items: center; gap: 6px;
    font-size: 12px; line-height: 16px; color: var(--text-light);
  }
  .contact-list svg { width: 8px; height: 8px; flex: none; }

  .social-list {
    position: absolute; right: 30px; top: 206px;
    display: flex; gap: 14px; list-style: none;
  }
  .social-list li { font-size: 11px; font-weight: 600; color: var(--text-light); }

  .bottom-bands { position: absolute; left: 0; bottom: 0; }

  .back-texture { position: absolute; inset: 0; background: linear-gradient(135deg, var(--orange), var(--orange-deep)); }
  .tagline {
    position: absolute; left: 0; right: 0; top: 224px; text-align: center;
    font-size: 12px; font-weight: 600; color: var(--white); text-transform: uppercase;
  }
</style>
</head>
<body>
  <section class="card card--front">
    <svg class="name-accent" width="24" height="30" viewBox="0 0 24 30">
      <polygon points="0,0 10,0 10,30 0,30" fill="var(--orange)"/>
      <polygon points="12,0 24,0 24,30 18,30" fill="var(--grey-band)"/>
    </svg>
    <h1 class="holder-name">Marcus Dalton</h1>
    <p class="holder-title">Managing Director</p>

    <p class="brand-name">Cellar Crafters</p>

    <ul class="contact-list">
      <li><svg viewBox="0 0 8 8"><rect x="2" y="0" width="4" height="8" rx="1" fill="var(--orange)"/></svg>302.418.7650</li>
      <li><svg viewBox="0 0 8 8"><rect x="0" y="1.5" width="8" height="5.5" fill="var(--orange)"/><polyline points="0,1.5 4,4.5 8,1.5" fill="none" stroke="var(--card-dark)" stroke-width="1"/></svg>cellarcrafters4u@examplemail.com</li>
      <li><svg viewBox="0 0 8 8"><circle cx="4" cy="4" r="4" fill="var(--orange)"/></svg>cellarcrafters4u.com</li>
    </ul>

    <ul class="social-list">
      <li>Friendloop</li>
      <li>HouseGuidr</li>
    </ul>

    <svg class="bottom-bands" width="440" height="21" viewBox="0 0 440 21">
      <polygon points="0,7 216,7 208,21 0,21" fill="var(--orange)"/>
      <polygon points="222,1 440,1 440,21 208,21" fill="var(--grey-band)"/>
    </svg>
  </section>

  <section class="card card--back">
    <div class="back-texture" role="img" aria-label="Faint tonal chevron texture across the orange card"></div>
    <p class="brand-name">Cellar Crafters</p>
    <p class="tagline">Specializing in finishing and remodeling basements.</p>
  </section>
</body>
</html>
```